Switch Kit - Banking Flyer

We want a design for an 8.5x11" flyer that matches the look of our website (www.morvellcommercebank.com). Outline is attached, but please feel free to include images/pictures/graphics that you think makes this easy to understand. The goal is to hand this flyer to a potential customer to get them to understand the information easily and quickly.

```html
<!DOCTYPE html>
<html lang="en">
<head>
<meta charset="UTF-8">
<title>Switch Kit – Morvell Commerce Bank</title>
<link href="https://fonts.googleapis.com/css2?family=Outfit:wght@400;500;700;800&display=swap" rel="stylesheet">
<style>
  :root {
    --page-bg: #ffffff;
    --navy: #22385a;
    --navy-deep: #1b2d4a;
    --navy-band: #2b4a73;
    --orange: #fbb034;
    --white: #ffffff;
  }
  * { box-sizing: border-box; margin: 0; padding: 0; }
  html, body {
    width: 1200px; height: 1200px; overflow: hidden;
    background: var(--page-bg);
    font-family: "Outfit", sans-serif;
  }
  .flyer {
    position: absolute; left: 238px; top: 88px;
    width: 724px; height: 1025px;
    background: linear-gradient(180deg, var(--navy-deep) 0%, var(--navy) 55%, var(--navy-deep) 100%);
    overflow: hidden; color: var(--white);
  }
  .hero-photo {
    position: absolute; left: 0; top: 90px; width: 724px; height: 500px;
    background:
      radial-gradient(ellipse 200px 190px at 440px 200px, rgba(251,176,52,.42), rgba(251,176,52,0) 70%),
      radial-gradient(ellipse 320px 260px at 480px 270px, rgba(120,145,180,.33), rgba(120,145,180,0) 75%),
      linear-gradient(180deg, rgba(34,56,90,0) 0%, rgba(60,84,120,.3) 50%, rgba(34,56,90,0) 100%);
  }
  .brand {
    position: absolute; left: 34px; top: 48px;
    display: flex; align-items: center; gap: 9px;
    font-weight: 700; font-size: 19px; letter-spacing: 1.6px; color: var(--white);
  }
  .brand-mark { width: 12px; height: 12px; border-radius: 50%; background: var(--white); }
  .headline {
    position: absolute; left: 35px; top: 278px; width: 520px;
    font-weight: 800; font-size: 36px; line-height: 46.6px;
    letter-spacing: -0.5px; text-transform: uppercase;
  }
  .step { position: absolute; left: 0; width: 724px; }
  .step-icon { position: absolute; }
  .step-rule { position: absolute; left: 113px; top: 0; width: 2px; background: var(--orange); }
  .step-body { position: absolute; left: 122px; top: 4px; font-size: 12.6px; line-height: 15.2px; color: var(--white); }
  .step-title {
    font-weight: 800; font-size: 12.4px; line-height: 12.6px; color: var(--orange);
    text-transform: uppercase; letter-spacing: -0.2px; margin-bottom: 2px;
  }
  .step-body p + p { margin-top: 7.8px; }
  .step-body strong { color: var(--orange); font-weight: 800; }
  .footer-band {
    position: absolute; left: 0; top: 934px; width: 724px; height: 91px;
    background: linear-gradient(90deg, var(--navy-band), var(--navy) 80%);
  }
  .contact { position: absolute; left: 81px; font-size: 14.5px; line-height: 16px; font-weight: 500; }
  .contact-icon { position: absolute; left: 0; }
  .contact-text { position: absolute; left: 42px; white-space: nowrap; }
  .web-panel { position: absolute; left: 0; top: 0; }
  .web-cta { position: absolute; left: 446px; top: 940px; width: 250px; color: var(--navy); text-align: center; }
  .web-cta .label { font-weight: 800; font-size: 29px; line-height: 32px; letter-spacing: -0.3px; }
  .web-cta .url { font-weight: 700; font-size: 15px; line-height: 18px; }
</style>
</head>
<body>
<main class="flyer">
  <div class="hero-photo" role="img" aria-label="Photo of hands using a laptop with a glowing account-switching interface and banking icons overlaid"></div>

  <div class="brand"><span class="brand-mark"></span>MORVELL COMMERCE BANK</div>

  <h1 class="headline">We look forward to creating an exceptional experience for you at Morvell Commerce Bank.</h1>

  <section class="step" style="top:513px;">
    <svg class="step-icon" style="left:35px; top:10px;" width="63" height="60" viewBox="0 0 70 66" aria-hidden="true">
      <path d="M36 8 A26 26 0 1 1 22 54" fill="none" stroke="#fff" stroke-width="4" stroke-linecap="round"/>
      <circle cx="16" cy="33" r="7" fill="none" stroke="#fbb034" stroke-width="4"/>
      <path d="M23 33 H46 M38 33 V40 M44 33 V38" stroke="#fbb034" stroke-width="4" stroke-linecap="round"/>
    </svg>
    <div class="step-rule" style="height:80px;"></div>
    <div class="step-body" style="width:318px;">
      <h2 class="step-title">Open a Morvell Commerce Bank account</h2>
      <p>Stop by our branch and visit with our knowledgeable team to open your new account. We will be happy to assist you in choosing the right account for your banking needs.</p>
    </div>
  </section>

  <section class="step" style="top:620px;">
    <svg class="step-icon" style="left:26px; top:67px;" width="73" height="48" viewBox="0 0 82 54" aria-hidden="true">
      <g stroke="#fff" stroke-width="3.5" stroke-linecap="round">
        <path d="M10 8 H22 M2 18 H18 M6 28 H20 M2 38 H18 M10 48 H22"/>
      </g>
      <circle cx="54" cy="27" r="22" fill="none" stroke="#fff" stroke-width="3.5" stroke-dasharray="9 5"/>
      <circle cx="54" cy="27" r="15" fill="#fbb034"/>
      <text x="54" y="34" text-anchor="middle" font-family="Outfit, sans-serif" font-weight="800" font-size="20" fill="#22385a">$</text>
    </svg>
    <div class="step-rule" style="height:171px;"></div>
    <div class="step-body" style="width:500px;">
      <h2 class="step-title">Stop using your old account and redirect your<br>automatic payments and direct deposits</h2>
      <p style="margin-top:4px;">It is important to remember to keep your old account open to ensure all your outstanding checks, deposits, and automatic withdrawals have cleared.</p>
      <p>We will provide you with a <strong>Payments Checklist</strong> to help you determine the companies you may need to notify of your account change so they can redirect any deposits or automatic withdrawals.</p>
      <p>Our <strong>Direct Deposit Change Notification and Notification of Automatic Withdrawal Change</strong> forms will easily allow companies to redirect your direct deposit(s) and automatic withdrawals to your new Morvell Commerce Bank account.</p>
    </div>
  </section>

  <section class="step" style="top:809px;">
    <svg class="step-icon" style="left:40px; top:16px;" width="60" height="56" viewBox="0 0 70 64" aria-hidden="true">
      <path d="M11 18 L35 4 L59 18 Z" fill="#fff"/>
      <rect x="12" y="21" width="46" height="4" fill="#fff"/>
      <rect x="15" y="28" width="5" height="22" fill="#fff"/>
      <rect x="50" y="28" width="5" height="22" fill="#fff"/>
      <text x="35" y="48" text-anchor="middle" font-family="Outfit, sans-serif" font-weight="800" font-size="24" fill="#fbb034">$</text>
      <rect x="10" y="53" width="50" height="4" fill="#fff"/>
      <rect x="6" y="59" width="58" height="3" fill="#fff"/>
    </svg>
    <div class="step-rule" style="height:90px;"></div>
    <div class="step-body" style="width:520px;">
      <h2 class="step-title">Close your old account</h2>
      <p style="margin-top:6px;">Now you are ready to switch. We will even provide an Account Closure Authorization form to close your old account. Any remaining account balance will be transferred to your Morvell Commerce Bank account.</p>
    </div>
  </section>

  <div class="footer-band"></div>

  <div class="contact" style="top:949px;">
    <svg class="contact-icon" width="22" height="28" viewBox="0 0 24 30" aria-hidden="true">
      <path d="M12 1 C5.5 1 1 5.8 1 11.5 C1 19 12 29 12 29 C12 29 23 19 23 11.5 C23 5.8 18.5 1 12 1 Z" fill="#fff"/>
      <circle cx="12" cy="11.5" r="4.5" fill="#2b4a73"/>
    </svg>
    <div class="contact-text">2740 East Harlow Avenue, Suite 310<br>Mesa Verde, AZ 85019</div>
  </div>
  <div class="contact" style="top:986px;">
    <svg class="contact-icon" width="23" height="23" viewBox="0 0 25 25" aria-hidden="true">
      <rect width="25" height="25" rx="4" fill="#fff"/>
      <path d="M8 5 L10.5 9.5 L9 11 C10 13.5 11.5 15 14 16 L15.5 14.5 L20 17 L18.5 20 C12 20 5 13 5 6.5 Z" fill="#2b4a73"/>
    </svg>
    <div class="contact-text" style="top:3px;">480.555.0142</div>
  </div>

  <svg class="web-panel" width="724" height="1025" viewBox="0 0 724 1025" aria-hidden="true">
    <polygon points="405,894 724,909 724,1025 439,1025" fill="#fbb034"/>
  </svg>
  <div class="web-cta">
    <div class="label">Visit Our Website:</div>
    <div class="url">www.morvellcommercebank.com</div>
  </div>
</main>
</body>
</html>
```